Lucivane signs for fridge and desk

I require 3 a4 designs very basic designs with single colour and easy to print. I have atached a style guide to see the fonts I used in my last three design. Please remember I'm printing in only one colour
PLease see the following link, of what I sell on tolvaro. I will be selling this allong side these products.
https://www.tolvaro.com/gp/product/K38N2XRDMV
Please see my competitors
https://www.tolvaro.com/Planner-Magnetic-Calendar-Refrigerator-Container/dp/K9QWRT4HZP/ref=sr_1_8?keywords=acrylic%2Bnote%2Bboard%2Brefrigerator%2Bdry%2Berase%2Bboard%2Bmagnetic%2Bclear&qid=1593816420&sr=8-8&th=1
and
https://www.tolvaro.com/Magnetic-Acrylic-Calendar-Fridge-Refrigerator/dp/K7MXPD2VQS/ref=sr_1_4_sspa?keywords=acrylic+note+board+refrigerator+dry+erase+board+magnetic+clear&qid=1593816377&sr=8-4-spons&psc=1&spLa=QmV0YVZhbHVlT25lVHdvVGhyZWVGb3VyRml2ZVNpeFNldmVuRWlnaHROaW5lVGVuRWxldmVuVHdlbHZlVGhpcnRlZW5Gb3VydGVlbkZpZnRlZW5TaXh0ZWVuU2V2ZW50ZWVuRWlnaHRlZW5OaW5ldGVlblR3ZW50eVR3ZW50eU9uZVR3ZW50eVR3b1R3ZW50eVRocmVlVHdlbnR5Rm91clR3ZW50eUZpdmVUd2VudHlTaXhUd2VudHlTZXZlbg==
I'd like something more fun and different. But that can still be printed on Lucivane with one colour and be functional. A shopping list, a weekly planner(both that stick to a fridge) and a to do list that will sit on a desk or kitchen counter top.
PLease design
1st a4
Break into seven parts, with seven headings..... Monday to Sunday.... here customers will be able to write menus and upcoming events. I want this landcape
2nd a4
'Shopping List' is to be the heading
I want this landcape
3rd a4
'To Do List' is the only text I would like
I would like this portrat and lines marked and a check box on the left hand side
Remember I can only print on the acrylic with one colour. I want to be different from my competitors but I do want to be functional.
just a reminder. I can only print with one colour

```html
<!DOCTYPE html>
<html lang="en">
<head>
<meta charset="utf-8">
<title>To Do List</title>
<link rel="stylesheet" href="https://fonts.googleapis.com/css2?family=Kaushan+Script&display=swap">
<style>
  :root {
    --ink: #000000;
    --paper: #ffffff;
  }
  * { box-sizing: border-box; margin: 0; padding: 0; }
  html, body {
    width: 839px;
    height: 1200px;
    overflow: hidden;
    background: var(--paper);
  }
  .board {
    position: absolute;
    left: 50px;
    top: 46px;
    width: 740px;
    height: 1108px;
    border: 3.5px solid var(--ink);
    border-radius: 20px;
    background: var(--paper);
  }
  .board-title {
    height: 112px;
    padding-top: 14px;
    text-align: center;
    font-family: "Kaushan Script", cursive;
    font-weight: 400;
    font-size: 70px;
    line-height: 1.1;
    color: var(--ink);
    letter-spacing: 1px;
  }
  .task-list {
    list-style: none;
    margin: 0 30px;
  }
  .task {
    position: relative;
    height: 80px;
    border-top: 2px solid var(--ink);
  }
  .task-box {
    position: absolute;
    left: 24px;
    top: 22px;
    width: 33px;
    height: 33px;
    border: 2.5px solid var(--ink);
  }
</style>
</head>
<body>
  <main class="board">
    <h1 class="board-title">To Do List</h1>
    <ul class="task-list">
      <li class="task"><span class="task-box"></span></li>
      <li class="task"><span class="task-box"></span></li>
      <li class="task"><span class="task-box"></span></li>
      <li class="task"><span class="task-box"></span></li>
      <li class="task"><span class="task-box"></span></li>
      <li class="task"><span class="task-box"></span></li>
      <li class="task"><span class="task-box"></span></li>
      <li class="task"><span class="task-box"></span></li>
      <li class="task"><span class="task-box"></span></li>
      <li class="task"><span class="task-box"></span></li>
      <li class="task"><span class="task-box"></span></li>
      <li class="task"><span class="task-box"></span></li>
    </ul>
  </main>
</body>
</html>
```